Corvane Holdings , new business card design

investment firm with corporate clients . need double sided business card , vertical and horizontal options ,logo must be clear. prefer pantone colors only and sharp design. website also www.corvane.ae

Khalid Bin Tarrafi
Managing Director
Tel. +971 4 387 2940
Mobile +971 50 518 2403
khalid@corvane.ae
Q-Span Plaza, officw 18-B07, Warqa Gardens, Dubai

Contact Information for Business Card

Khalid Bin Tarrafi
Managing Director

Font styles to use
Serif

Colors

Designer to choose colors to be used in the design.

```html
<!DOCTYPE html>
<html lang="en">
<head>
<meta charset="utf-8">
<title>Corvane Holdings – Business Card</title>
<link rel="stylesheet" href="https://fonts.googleapis.com/css2?family=Questrial&display=swap">
<style>
  :root {
    --navy: #06245e;
    --steel: #4f77a3;
    --paper: #ffffff;
    --ink-grey: #555a63;
    --backdrop: #e6e4e2;
    --logo-light: #dfe4ec;
  }
  * { margin: 0; padding: 0; box-sizing: border-box; }
  html, body {
    width: 1200px; height: 997px; overflow: hidden;
    background: var(--backdrop);
    font-family: "Questrial", "Century Gothic", sans-serif;
  }
  .card {
    position: absolute;
    left: 340px;
    width: 520px; height: 289px;
    box-shadow: 0 6px 18px rgba(0,0,0,0.12);
    overflow: hidden;
  }
  .card--front { top: 150px; background: var(--paper); }
  .card--back { top: 545px; background: var(--navy); }

  .wordmark {
    font-size: 25px;
    letter-spacing: 2px;
    white-space: nowrap;
  }
  .card--front .wordmark {
    position: absolute; left: 46px; top: 52px;
    color: var(--navy);
  }
  .card--back .wordmark {
    position: absolute; left: 0; right: 0; top: 126px;
    text-align: center;
    color: var(--logo-light);
    font-size: 28px;
  }

  .holder { position: absolute; left: 46px; top: 120px; }
  .holder__name { color: var(--navy); font-size: 17px; font-weight: 700; }
  .holder__title { color: var(--ink-grey); font-size: 12px; margin-top: 1px; }

  .contacts { position: absolute; left: 46px; top: 165px; list-style: none; }
  .contacts li {
    display: flex; align-items: center; gap: 7px;
    color: var(--ink-grey); font-size: 11px; line-height: 16px;
  }
  .contacts svg { width: 11px; height: 11px; flex: none; }

  .footer-band { position: absolute; left: 0; bottom: 0; width: 520px; height: 60px; }
  .website {
    position: absolute; right: 22px; bottom: 24px;
    color: #fff; font-size: 12px; letter-spacing: 2px;
  }
</style>
</head>
<body>

<section class="card card--front" aria-label="Business card front">
  <div class="wordmark">Corvane Holdings</div>

  <div class="holder">
    <div class="holder__name">Khalid Bin Tarrafi</div>
    <div class="holder__title">Managing Director</div>
  </div>

  <ul class="contacts">
    <li>
      <svg viewBox="0 0 12 12" aria-hidden="true"><rect width="12" height="12" rx="2" fill="var(--navy)"/><path d="M3.5 3h1.6l.7 1.8-1 .7a4.5 4.5 0 0 0 1.9 1.9l.7-1 1.8.7V8.7C9.2 9.2 8.6 9.5 8 9.4 5.4 9 3 6.6 2.6 4c0-.5.3-1 .9-1z" fill="#fff"/></svg>
      +971 4 387 2940
    </li>
    <li>
      <svg viewBox="0 0 12 12" aria-hidden="true"><rect width="12" height="12" rx="2" fill="var(--navy)"/><rect x="4" y="2.3" width="4" height="7.4" rx=".7" fill="none" stroke="#fff" stroke-width=".9"/><circle cx="6" cy="8.3" r=".5" fill="#fff"/></svg>
      +971 50 518 2403
    </li>
    <li>
      <svg viewBox="0 0 12 12" aria-hidden="true"><rect width="12" height="12" rx="2" fill="var(--navy)"/><rect x="2.5" y="3.5" width="7" height="5" fill="none" stroke="#fff" stroke-width=".9"/><path d="M2.5 3.5 6 6.4l3.5-2.9" fill="none" stroke="#fff" stroke-width=".9"/></svg>
      khalid@corvane.ae
    </li>
    <li>
      <svg viewBox="0 0 12 12" aria-hidden="true"><rect width="12" height="12" rx="2" fill="var(--navy)"/><path d="M6 2.2a2.5 2.5 0 0 0-2.5 2.5C3.5 6.6 6 9.8 6 9.8s2.5-3.2 2.5-5.1A2.5 2.5 0 0 0 6 2.2z" fill="#fff"/><circle cx="6" cy="4.7" r=".9" fill="var(--navy)"/></svg>
      Q-Span Plaza, officw 18-B07, Warqa Gardens, Dubai
    </li>
  </ul>

  <svg class="footer-band" viewBox="0 0 520 60" aria-hidden="true">
    <polygon points="0,46 300,46 300,60 0,60" fill="var(--steel)"/>
    <polygon points="340,10 520,10 520,60 290,60" fill="var(--navy)"/>
  </svg>
  <div class="website">www.corvane.ae</div>
</section>

<section class="card card--back" aria-label="Business card back">
  <div class="wordmark">Corvane Holdings</div>
</section>

</body>
</html>
```